1876 Basins & Spouts Business Card

I'm wanting to get a business card designed. Our business is 1876 Basins & Spouts
Details for the card:

1876 Basins & Spouts
Name: Harold Vesk
Email: harold@1876basinsandspouts.com.au
Website: www.1876basinsandspouts.com.au
Mobile: 0438 260 947
Phone: 02 7481 3926

Font of Basins & Spouts is called Snell Roundhand. Not sue what font logo text is.

I'm thinking two sided but it doesn't have to be.

```html
<!DOCTYPE html>
<html lang="en">
<head>
<meta charset="utf-8">
<title>1876 Basins &amp; Spouts — Business Card</title>
<link rel="stylesheet" href="https://fonts.googleapis.com/css2?family=Lato:wght@400;700&family=Montserrat:wght@600&display=swap">
<style>
  :root {
    --ink: #231f20;
    --paper: #ffffff;
    --stage: #e9e8e6;
    --soft-ink: #555555;
  }
  * { box-sizing: border-box; margin: 0; padding: 0; }
  html, body { width: 1200px; height: 912px; overflow: hidden; }
  body {
    background: var(--stage);
    font-family: "Lato", sans-serif;
    display: flex;
    align-items: center;
    justify-content: center;
    gap: 40px;
  }
  .card {
    position: relative;
    width: 540px;
    height: 309px;
    border-radius: 16px;
    overflow: hidden;
    background: var(--ink);
    box-shadow: 0 6px 18px rgba(0,0,0,.18);
  }
  /* back side */
  .card-back { display: flex; align-items: center; justify-content: center; }
  .brand-mark {
    display: flex; flex-direction: column; align-items: center; gap: 14px;
    color: var(--paper);
  }
  .brand-mark .dot {
    width: 54px; height: 54px; border-radius: 50%;
    border: 1.5px solid var(--paper);
  }
  .brand-mark .name {
    font-size: 26px; font-weight: 400; letter-spacing: .5px;
  }
  /* front side */
  .card-front .swoosh { position: absolute; inset: 0; }
  .lockup {
    position: absolute; top: 34px; left: 268px;
    display: flex; align-items: center; gap: 10px;
    color: var(--ink);
  }
  .lockup .dot {
    width: 34px; height: 34px; border-radius: 50%;
    border: 1.2px solid var(--ink); flex: none;
  }
  .lockup .name { font-size: 17px; font-weight: 400; line-height: 1.1; }
  .lockup .tagline { font-size: 8.5px; color: var(--soft-ink); margin-top: 3px; }
  .contact {
    position: absolute; left: 28px; bottom: 18px;
    color: var(--paper);
  }
  .contact .person {
    font-family: "Montserrat", sans-serif; font-weight: 600;
    font-size: 20px; letter-spacing: 1px; text-transform: uppercase;
  }
  .contact .role { font-size: 14px; margin-bottom: 8px; }
  .contact .address { font-size: 14px; line-height: 1.3; margin-bottom: 8px; }
  .contact ul { list-style: none; font-size: 14px; line-height: 1.45; }
  .contact li { display: flex; align-items: center; gap: 8px; }
  .contact li svg { width: 11px; height: 11px; flex: none; }
</style>
</head>
<body>

  <section class="card card-back" aria-label="Card back">
    <div class="brand-mark">
      <span class="dot"></span>
      <span class="name">1876 Basins &amp; Spouts</span>
    </div>
  </section>

  <section class="card card-front" aria-label="Card front">
    <svg class="swoosh" viewBox="0 0 540 309" preserveAspectRatio="none" aria-hidden="true">
      <path d="M232 0 Q300 205 540 232 L540 0 Z" fill="#ffffff"/>
      <path d="M232 0 Q300 205 540 232" fill="none" stroke="#231f20" stroke-width="8"/>
      <path d="M222 0 Q292 218 540 244" fill="none" stroke="#ffffff" stroke-width="2"/>
    </svg>

    <div class="lockup">
      <span class="dot"></span>
      <div>
        <div class="name">1876 Basins &amp; Spouts</div>
        <div class="tagline">Classic elegance paired with everyday function</div>
      </div>
    </div>

    <div class="contact">
      <div class="person">Harold Vesk</div>
      <div class="role">Director</div>
      <div class="address">PO Box 48 Mount<br>Ashby NSW 2791</div>
      <ul>
        <li>
          <svg viewBox="0 0 12 12"><path d="M2.5 1 L4.5 1 L5.2 3.4 L4 4.4 Q5 6.6 7.6 8 L8.6 6.8 L11 7.5 L11 9.5 Q10.5 11 9 11 Q1 10 1 2.5 Q1 1 2.5 1 Z" fill="#fff"/></svg>
          0438 260 947
        </li>
        <li>
          <svg viewBox="0 0 12 12"><rect x="3" y="0.8" width="6" height="10.4" rx="1" fill="none" stroke="#fff" stroke-width="1.2"/><circle cx="6" cy="9.4" r=".7" fill="#fff"/></svg>
          02 7481 3926
        </li>
        <li>
          <svg viewBox="0 0 12 12"><rect x="1" y="2.5" width="10" height="7" fill="none" stroke="#fff" stroke-width="1.1"/><path d="M1 2.5 L6 6.5 L11 2.5" fill="none" stroke="#fff" stroke-width="1.1"/></svg>
          harold@1876basinsandspouts.com.au
        </li>
        <li>
          <svg viewBox="0 0 12 12"><circle cx="6" cy="6" r="5" fill="none" stroke="#fff" stroke-width="1.1"/><ellipse cx="6" cy="6" rx="2.2" ry="5" fill="none" stroke="#fff" stroke-width="1"/><path d="M1 6 H11" stroke="#fff" stroke-width="1"/></svg>
          www.1876basinsandspouts.com.au
        </li>
      </ul>
    </div>
  </section>

</body>
</html>
```